Financial Advisor Resource Firm needs business card design

Need business card design for company in Omaha NE called Meridale Circle. We provide resources to financial advisors....workshop programs, retirement analysis, and insurance planning. I would like to see designs that use grays, greens, black, and white colors. The final design should communicate 'collaboration' and be simple yet attractive to financial planning clients. I will attached our logo and another picture of a puzzle piece coming together. I would like the incorporate the puzzle picture somehow, maybe on the back somehow, with color or just the gray scale....OR, the picture be the front of the card with 'Meridale' definition on it (see upload) and then company logo, employee name, title, address on the back (see ppt uploaded). The following disclosure needs to be included somewhere- Advisory services offered through Stonebrook Assets, LLC.
Updates

I uploaded a svg and ai file of the logo

Target Market(s)

Financial planning clients and financial advisors....so pretty diverse age range of about 40-70.

Industry/Entity Type

Financial Planning

Contact Information for Business Card

Tobias L. Fenwright, MBA
Founder/President
5287 E. Larkin Road
Suite 230
Omaha, NE 68190
Phone- (402) 555-0147
Cell- (402) 555-0183
Fax- (402) 555-0129
email- tobias@meridaleplan.example
web address- www.meridaleplan.example

Colors
1b1b1b
474747
d3d3d3
ffffff
9bcb3c
abd036

Requirements
Must have
• Must include logo provided, must be 2 sided, and must have disclosure...all of these items listed in project description

```html
<!DOCTYPE html>
<html lang="en">
<head>
<meta charset="utf-8">
<title>Meridale Circle — Business Card</title>
<link href="https://fonts.googleapis.com/css2?family=Montserrat:wght@400;500;600&display=swap" rel="stylesheet">
<style>
  :root {
    --ink: #1b1b1b;
    --graphite: #474747;
    --mist: #d3d3d3;
    --paper: #ffffff;
    --leaf: #9bcb3c;
    --lime: #abd036;
    --backdrop: #e9e9e7;
  }
  * { box-sizing: border-box; margin: 0; padding: 0; }
  html, body { width: 1200px; height: 715px; overflow: hidden; }
  body {
    background: var(--backdrop);
    font-family: "Montserrat", Arial, sans-serif;
    position: relative;
  }
  .card {
    position: absolute;
    top: 215px;
    width: 500px;
    height: 286px;
    overflow: hidden;
    box-shadow: 0 6px 18px rgba(0,0,0,0.18);
  }
  .card-back { left: 60px; background: var(--ink); }
  .card-front { left: 640px; background: var(--paper); }

  .wordmark {
    display: flex;
    align-items: center;
    gap: 10px;
    font-weight: 600;
    letter-spacing: 0.08em;
    text-transform: uppercase;
    white-space: nowrap;
  }
  .wordmark .dot {
    width: 14px; height: 14px; border-radius: 50%;
    background: var(--leaf);
    flex: none;
  }
  .card-back .wordmark {
    position: absolute;
    left: 50%; top: 50%;
    transform: translate(-50%, -50%);
    color: var(--paper);
    font-size: 30px;
  }
  .card-front .wordmark {
    position: absolute;
    left: 26px; top: 48px;
    color: var(--ink);
    font-size: 20px;
  }
  .card-front .wordmark .dot { width: 11px; height: 11px; }

  .swoosh { position: absolute; inset: 0; }

  .rule {
    position: absolute;
    height: 1px;
    background: var(--ink);
  }
  .rule-top { left: 22px; top: 96px; width: 290px; }
  .rule-name { right: 22px; top: 214px; width: 185px; }

  .contacts {
    position: absolute;
    left: 26px; top: 108px;
    list-style: none;
    font-size: 11.5px;
    line-height: 17px;
    color: var(--ink);
  }
  .contacts li { display: flex; align-items: center; gap: 8px; }
  .contacts svg { width: 9px; height: 9px; flex: none; fill: var(--leaf); }
  .contacts .accent { color: var(--leaf); }

  .person {
    position: absolute;
    right: 22px; top: 166px;
    text-align: right;
  }
  .person .name {
    color: var(--leaf);
    font-size: 19px;
    font-weight: 500;
    line-height: 24px;
  }
  .person .title {
    color: var(--ink);
    font-size: 12px;
    line-height: 18px;
  }

  .address {
    position: absolute;
    right: 22px; bottom: 22px;
    text-align: right;
    font-size: 12px;
    font-style: normal;
    line-height: 17px;
    color: var(--ink);
  }

  .disclosure {
    position: absolute;
    left: 26px; bottom: 22px;
    width: 190px;
    font-size: 8px;
    line-height: 11px;
    color: var(--graphite);
  }
</style>
</head>
<body>

  <section class="card card-back" aria-label="Card back">
    <div class="wordmark"><span class="dot"></span>Meridale Circle</div>
  </section>

  <section class="card card-front" aria-label="Card front">
    <svg class="swoosh" viewBox="0 0 500 286" aria-hidden="true">
      <path d="M70,0 L300,0 C230,6 150,9 70,0 Z" fill="var(--lime)"/>
      <path d="M215,0 L500,0 L500,138 C425,136 385,112 345,74 C300,32 265,8 215,0 Z" fill="var(--leaf)"/>
      <path d="M80,14 C200,14 270,22 320,70 C370,118 410,148 500,150" fill="none" stroke="var(--ink)" stroke-width="10"/>
    </svg>

    <div class="wordmark"><span class="dot"></span>Meridale Circle</div>
    <div class="rule rule-top"></div>

    <ul class="contacts">
      <li><svg viewBox="0 0 10 10"><path d="M2 0.5 L4 2.5 L3 3.8 C3.8 5.3 4.8 6.3 6.2 7 L7.5 6 L9.5 8 L8 9.5 C4 9 1 6 0.5 2 Z"/></svg>(402) 555-0147</li>
      <li><svg viewBox="0 0 10 10"><rect x="2.5" y="0.5" width="5" height="9" rx="1"/></svg>(402) 555-0183</li>
      <li><svg viewBox="0 0 10 10"><rect x="0.5" y="3.5" width="9" height="5" rx="1"/><rect x="2.5" y="0.5" width="5" height="3"/></svg>(402) 555-0129</li>
      <li><svg viewBox="0 0 10 10"><path d="M0.5 2 H9.5 V8 H0.5 Z M0.5 2 L5 5.5 L9.5 2" fill="none" stroke="var(--leaf)" stroke-width="1.2"/></svg>tobias@meridaleplan.example</li>
      <li><svg viewBox="0 0 10 10"><circle cx="5" cy="5" r="4.2" fill="none" stroke="var(--leaf)" stroke-width="1.2"/><path d="M0.8 5 H9.2 M5 0.8 V9.2" stroke="var(--leaf)" stroke-width="0.9"/></svg><span>www.<span class="accent">meridaleplan</span>.example</span></li>
    </ul>

    <div class="person">
      <p class="name">Tobias L. Fenwright, MBA</p>
      <p class="title">Founder/President</p>
    </div>
    <div class="rule rule-name"></div>

    <p class="disclosure">Advisory services offered through Stonebrook Assets, LLC.</p>

    <address class="address">
      5287 E. Larkin Road<br>
      Suite 230 Omaha, NE 68190
    </address>
  </section>

</body>
</html>
```